New Business card design to reflect rebrand

I would like a business card design with a good base colour for our new logo and also a placeholder for a profile pic of the card holder. the design needs to be editable to the point that we can easily change the picture of the person and use that design for printmerlo etc. we are looking at a metalic finish business card so will need a good base colour to bring out the finish.

Target Market(s)

prospective customers

Industry/Entity Type

Business

Contact Information for Business Card

I would like one editable design that we can change the name of the card holder and profile picture. The design need to be in a format that be send to printmerlo etc.

Our address is Fenwick Lodge, Copse Lane, Ashbury Vale, GU14 3TP Tel no. 01483 556172

Requirements
Must have
• place holder for a profile pic for the card holder. in AI or preferably PSD format

```html
<!DOCTYPE html>
<html lang="en">
<head>
<meta charset="utf-8">
<title>Northvane Workplace Services – Business Card</title>
<link rel="stylesheet" href="https://fonts.googleapis.com/css2?family=Open+Sans:wght@400;600;700&display=swap">
<style>
  :root {
    --brand-orange: #ee6405;
    --brand-slate: #3f5266;
    --card-white: #ffffff;
    --ink: #1e1e1e;
    --backdrop: #e9e6e3;
    --photo-dark: #2a2f3a;
    --photo-light: #d9d6d2;
  }
  * { box-sizing: border-box; margin: 0; padding: 0; }
  html, body { width: 1200px; height: 900px; overflow: hidden; }
  body {
    background: var(--backdrop);
    font-family: "Open Sans", Arial, sans-serif;
    position: relative;
  }
  .card {
    position: absolute;
    border-radius: 14px;
    overflow: hidden;
    box-shadow: 0 6px 18px rgba(0,0,0,0.18);
  }
  /* Front */
  .card--front {
    left: 78px; top: 34px; width: 587px; height: 364px;
    background: var(--card-white);
  }
  .card--front .band {
    position: absolute; left: 0; top: 25px; width: 100%; height: 99px;
    background: var(--brand-orange);
  }
  .card--front .logo-plate {
    position: absolute; left: 127px; top: 15px; width: 325px; height: 116px;
    border-radius: 58px; background: var(--card-white);
  }
  .wordmark {
    position: absolute; left: 0; width: 100%;
    text-align: center; font-weight: 700; line-height: 1;
  }
  .card--front .wordmark { color: var(--brand-slate); }
  .wordmark__name { top: 42px; font-size: 34px; letter-spacing: 1px; }
  .wordmark__tagline { top: 84px; font-size: 15px; letter-spacing: 3px; }
  .profile-photo {
    position: absolute; left: 15px; top: 138px; width: 207px; height: 226px;
    background: linear-gradient(180deg, var(--photo-light) 0%, #8a8c92 40%, var(--photo-dark) 100%);
  }
  .holder {
    position: absolute; left: 272px; top: 176px; color: var(--ink);
  }
  .holder__name {
    color: var(--brand-orange); font-weight: 600; font-size: 22px; line-height: 1;
    margin-bottom: 20px;
  }
  .contact-line {
    display: flex; align-items: center; gap: 8px;
    font-size: 15px; line-height: 25px;
  }
  .contact-line svg { width: 12px; height: 12px; flex: none; }
  .icon-phone { fill: var(--brand-orange); }
  .icon-mail rect { fill: var(--brand-orange); }
  .icon-mail path { fill: none; stroke: var(--card-white); stroke-width: 2.5; }
  .holder__address { font-size: 15px; line-height: 22px; margin-top: 12px; }
  /* Back */
  .card--back {
    left: 390px; top: 507px; width: 565px; height: 348px;
    background: var(--brand-orange);
  }
  .card--back .band {
    position: absolute; left: 0; top: 80px; width: 100%; height: 96px;
    background: var(--card-white);
  }
  .card--back .logo-plate {
    position: absolute; left: 118px; top: 70px; width: 327px; height: 116px;
    border-radius: 58px; background: var(--brand-orange);
  }
  .card--back .wordmark { color: var(--card-white); }
</style>
</head>
<body>
  <section class="card card--front" aria-label="Business card front">
    <div class="band"></div>
    <div class="logo-plate">
      <span class="wordmark wordmark__name">NORTHVANE</span>
      <span class="wordmark wordmark__tagline">WORKPLACE SERVICES</span>
    </div>
    <div class="profile-photo" role="img" aria-label="Profile photo of the card holder"></div>
    <div class="holder">
      <p class="holder__name">Daniel Hart</p>
      <p class="contact-line">
        <svg class="icon-phone" viewBox="0 0 24 24" aria-hidden="true"><path d="M6.6 10.8a15 15 0 0 0 6.6 6.6l2.2-2.2a1 1 0 0 1 1-.25 11.4 11.4 0 0 0 3.6.57 1 1 0 0 1 1 1V20a1 1 0 0 1-1 1A17 17 0 0 1 3 4a1 1 0 0 1 1-1h3.5a1 1 0 0 1 1 1c0 1.25.2 2.45.57 3.57a1 1 0 0 1-.25 1z"/></svg>
        01483 556172
      </p>
      <p class="contact-line">
        <svg class="icon-mail" viewBox="0 0 24 24" aria-hidden="true"><rect x="1" y="5" width="22" height="14"/><path d="M1 5l11 8 11-8"/></svg>
        info@northvane.com
      </p>
      <p class="holder__address">Fenwick Lodge, Copse Lane,<br>Ashbury Vale, GU14 3TP</p>
    </div>
  </section>

  <section class="card card--back" aria-label="Business card back">
    <div class="band"></div>
    <div class="logo-plate">
      <span class="wordmark wordmark__name">NORTHVANE</span>
      <span class="wordmark wordmark__tagline">WORKPLACE SERVICES</span>
    </div>
  </section>
</body>
</html>
```